Quillmere Supply Chain and Logistic Consulting

Please review the attached Business Card. I want as close to this card with the colors, fonts, and quality of the card as possible. The attached compass should replace the deer head on both sides of the card and the text should say:

Backside
Compass JPEG
Quillmere SC&L
A Supply Chain and Logistics Consulting Company

Frontside
Quillmere SC&L
Ray Falkner - Tampa Florida
President
____________________________________
(555) 314-9027
QuillmereSCL@Examplemail.com
_____________________________________

Bottom Front Side

Target Market(s)

Businesses

Contact Information for Business Card

Backside
Compass JPEG
Quillmere SC&L

Frontside
Quillmere SC&L
President
(555) 314-9027
QuillmereSCL@Examplemail.com

Bottom Front Side

Font styles to use
Serif
Script

Colors

Designer to choose colors to be used in the design.

Requirements
Must have
• See attached card for reference
Nice to have
Should not have

```html
<!DOCTYPE html>
<html lang="en">
<head>
<meta charset="utf-8">
<title>Quillmere SC&amp;L Business Card</title>
<link href="https://fonts.googleapis.com/css2?family=Cinzel:wght@400;500&family=Tinos&display=swap" rel="stylesheet">
<style>
  :root {
    --backdrop: #4b4c4c;
    --card: #1b1c1e;
    --ink: #f2f2f2;
    --ink-soft: #cfcfcf;
    --mark: #bdbdbd;
  }
  html, body {
    margin: 0;
    padding: 0;
    width: 963px;
    height: 1200px;
    overflow: hidden;
    background: var(--backdrop);
  }
  .card {
    position: absolute;
    left: 231px;
    width: 557px;
    height: 318px;
    background: var(--card);
    overflow: hidden;
    color: var(--ink);
  }
  .card--front { top: 221px; }
  .card--back { top: 636px; }

  .brand {
    position: absolute;
    left: 0;
    width: 100%;
    text-align: center;
    font-family: "Tinos", serif;
    font-weight: 400;
    color: var(--ink);
  }
  .brand__name {
    margin: 0;
    font-weight: 400;
    line-height: 1;
  }
  .brand__tagline {
    margin: 6px 0 0;
    font-size: 11px;
    font-weight: 400;
    line-height: 1;
    color: var(--ink-soft);
  }
  .card--front .brand { top: 98px; }
  .card--front .brand__name { font-size: 32px; }

  .person {
    position: absolute;
    right: 310px;
    top: 185px;
    text-align: right;
    font-family: "Cinzel", serif;
    line-height: 1;
  }
  .person__name { font-size: 22px; font-weight: 500; letter-spacing: 0.5px; }
  .person__role { font-size: 14px; margin-top: 3px; letter-spacing: 0.8px; }

  .divider {
    position: absolute;
    left: 267px;
    top: 177px;
    width: 1px;
    height: 55px;
    background: var(--ink);
  }

  .contacts {
    position: absolute;
    left: 287px;
    top: 180px;
    margin: 0;
    padding: 0;
    list-style: none;
    font-family: "Tinos", serif;
    font-size: 13.5px;
  }
  .contacts li {
    display: flex;
    align-items: center;
    height: 18.5px;
  }
  .contacts svg {
    width: 11px;
    height: 11px;
    margin-right: 9px;
    fill: var(--ink);
  }

  .card--back .mark-disc {
    position: absolute;
    left: 231px;
    top: 75px;
    width: 95px;
    height: 95px;
    border-radius: 50%;
    background: var(--mark);
  }
  .card--back .brand { top: 220px; }
  .card--back .brand__name { font-size: 28px; }
  .card--back .brand__tagline { font-size: 10px; }
</style>
</head>
<body>

<section class="card card--front">
  <div class="brand">
    <h1 class="brand__name">Quillmere SC&amp;L</h1>
    <p class="brand__tagline">A supply chain &amp; logistics consulting company</p>
  </div>
  <div class="person">
    <div class="person__name">Ray Falkner</div>
    <div class="person__role">President</div>
  </div>
  <div class="divider"></div>
  <ul class="contacts">
    <li>
      <svg viewBox="0 0 24 24" aria-hidden="true"><path d="M6.6 10.8a15 15 0 0 0 6.6 6.6l2.2-2.2c.3-.3.7-.4 1-.2 1.1.4 2.3.6 3.6.6.6 0 1 .4 1 1V20c0 .6-.4 1-1 1A17 17 0 0 1 3 4c0-.6.4-1 1-1h3.5c.6 0 1 .4 1 1 0 1.3.2 2.5.6 3.6.1.3 0 .7-.2 1z"/></svg>
      (555) 314-9027
    </li>
    <li>
      <svg viewBox="0 0 24 24" aria-hidden="true"><path d="M2 5h20v14H2z M3 6l9 7 9-7" fill="none" stroke="#f2f2f2" stroke-width="2"/><path d="M2 5h20L12 12z"/></svg>
      QuillmereSCL@Examplemail.com
    </li>
    <li>
      <svg viewBox="0 0 24 24" aria-hidden="true"><circle cx="12" cy="12" r="10"/><path d="M2 12h20M12 2c3 3 3 17 0 20M12 2c-3 3-3 17 0 20" stroke="#1b1c1e" stroke-width="1.6" fill="none"/></svg>
      www.quillmerescl.com
    </li>
  </ul>
</section>

<section class="card card--back">
  <div class="mark-disc" aria-hidden="true"></div>
  <div class="brand">
    <h2 class="brand__name">Quillmere SC&amp;L</h2>
    <p class="brand__tagline">A supply chain &amp; logistics consulting company</p>
  </div>
</section>

</body>
</html>
```